Telecommunications/Power civil contractor needs business card design

Were a new telecommunications/power underground civil contractor that is looking for a new business card design. Our company colours are silver or grey and orange. Feel free to use the white background logo or the black background logo.

Target Market(s)

Local contractors, utility companies, private sector mining/energy companies, developers.

Industry/Entity Type

Telecommunications

Contact Information for Business Card

Each card will need the following info:
Persons name:
Title:
E-mail:
Phone number:
Shop Address:
Mailing Address:

Requirements
Must have
• Each card will need the following info:
• Persons name:
• Title:
• E-mail:
• Phone number:
• Shop Address:
• Mailing Address:

```html
<!DOCTYPE html>
<html lang="en">
<head>
<meta charset="utf-8">
<title>Trenchline Civil Inc — Business Card</title>
<link rel="stylesheet" href="https://fonts.googleapis.com/css2?family=Source+Sans+3:wght@400;600;700&display=swap">
<style>
  :root {
    --bg: #e9e7e4;
    --card: #ffffff;
    --band-grey: #6d6f6e;
    --orange: #f05a24;
    --text-grey: #5a5a5a;
    --ink: #1e1e1e;
  }
  html, body {
    margin: 0;
    width: 1200px;
    height: 900px;
    overflow: hidden;
    background: var(--bg);
    font-family: "Source Sans 3", "Myriad Pro", sans-serif;
  }
  .canvas { position: relative; width: 1200px; height: 900px; }

  .card {
    position: absolute;
    background: var(--card);
    box-shadow: 0 6px 18px rgba(0,0,0,0.18);
    overflow: hidden;
  }
  .band { position: absolute; left: 0; right: 0; }

  /* Contact side */
  .card-contact { left: 78px; top: 34px; width: 587px; height: 364px; }
  .card-contact .band { background: var(--band-grey); }
  .card-contact .band-top { top: 0; height: 41px; }
  .card-contact .band-bottom { bottom: 0; height: 45px; }

  .contact-body {
    position: absolute; left: 0; right: 0; top: 41px;
    text-align: center; color: var(--ink);
  }
  .person { margin-top: 20px; font-size: 23px; font-weight: 600; line-height: 1; }
  .person .first { color: var(--orange); }
  .person .last { color: var(--text-grey); }
  .person .divider { color: var(--text-grey); font-weight: 400; margin: 0 6px 0 4px; }
  .person .title { font-size: 17px; font-weight: 400; color: var(--ink); vertical-align: 2px; }

  .address-block { font-size: 16.5px; line-height: 19px; }
  .address-block .label { font-size: 19px; font-weight: 400; line-height: 22px; }
  .label .accent { color: var(--orange); }
  .label .rest { color: var(--text-grey); }
  .mailing { margin-top: 40px; }
  .shop { margin-top: 32px; }
  .contact-line { margin-top: 35px; font-size: 16.5px; }
  .contact-line .sep { margin: 0 6px; }

  /* Brand side */
  .card-brand { left: 388px; top: 506px; width: 566px; height: 351px; }
  .card-brand .band { background: var(--orange); }
  .card-brand .band-top { top: 0; height: 41px; }
  .card-brand .band-bottom { bottom: 0; height: 42px; }

  .brand-mark {
    position: absolute; left: 50%; top: 70px;
    width: 130px; height: 130px; margin-left: -65px;
  }
  .brand-name {
    position: absolute; left: 0; right: 0; top: 228px;
    text-align: center; color: var(--text-grey);
    font-size: 34px; font-weight: 700; letter-spacing: 2px; line-height: 1;
  }
</style>
</head>
<body>
<div class="canvas">

  <section class="card card-contact">
    <div class="band band-top"></div>
    <div class="contact-body">
      <div class="person">
        <span class="first">Marcus</span> <span class="last">Hale</span><span class="divider">|</span><span class="title">Managing Director</span>
      </div>
      <div class="address-block mailing">
        <div class="label"><span class="accent">Mailing</span> <span class="rest">Address</span></div>
        <div>12345, Address Goes Here Country Name, 123456</div>
      </div>
      <div class="address-block shop">
        <div class="label"><span class="accent">Shop</span> <span class="rest">Address</span></div>
        <div>12345, Address Goes Here Country Name, 123456</div>
      </div>
      <div class="contact-line">(055)-318-2046<span class="sep">|</span>office@trenchlinecivil.com</div>
    </div>
    <div class="band band-bottom"></div>
  </section>

  <section class="card card-brand">
    <div class="band band-top"></div>
    <svg class="brand-mark" viewBox="0 0 130 130" aria-hidden="true">
      <circle cx="65" cy="65" r="62" fill="none" stroke="var(--band-grey)" stroke-width="6"/>
    </svg>
    <div class="brand-name">TRENCHLINE CIVIL INC</div>
    <div class="band band-bottom"></div>
  </section>

</div>
</body>
</html>
```